BUSINESS CARD - HALLORAN FIELD SERVICES

I would like to create a business card for my fertilizer spreading business. I would like to incorporate my existing logo and also a description of the services offered. The business card will be given to farmers so must be kept simple but effective. It will also be left in stores so much also be eye catching in order to stand out from other cards.

Target Market(s)

FARMERS

Requirements
Must have
• FRONT OF CARD = EXISTING LOGO + "CUSTOMISED SPREADING" below the logo

REAR Of CARD = SERVICES OFFERED AND CONTACT DETAILS

- Bulk fertilizer including Lime, Gypsum, Manure & Compost
- Granular fertilizer including Single Super, Urea, Gran-am, & Custom Blends
- Modern equipment - Autosteer & Variable Rate Capable
- Friendly & Reliable Service
- Contact Gus: 0417 552 308
Nice to have
• utilize same color scheme as existing logo

```html
<!DOCTYPE html>
<html lang="en">
<head>
<meta charset="utf-8">
<title>Halloran Field Services – Business Card</title>
<link href="https://fonts.googleapis.com/css2?family=Montserrat:wght@500;700;800&family=Saira+Condensed:wght@500;600;700&display=swap" rel="stylesheet">
<style>
  :root{
    --orange:#f28a1c;
    --orange-deep:#e5780f;
    --ink:#1c1c1c;
    --grey:#5a5a5a;
    --white:#ffffff;
    --stage:#2a2d31;
  }
  *{box-sizing:border-box;margin:0;padding:0}
  html,body{width:1200px;height:900px;overflow:hidden;background:var(--stage)}
  .stage{width:1200px;height:900px;display:flex;flex-direction:column;align-items:center;justify-content:center;gap:48px}
  .card{width:630px;height:360px;border-radius:26px;position:relative;overflow:hidden;box-shadow:0 12px 30px rgba(0,0,0,.35)}

  /* Front */
  .card-front{background:var(--orange);display:flex;flex-direction:column;align-items:center;justify-content:center;color:var(--white)}
  .brand{display:flex;align-items:center;gap:18px}
  .brand-dot{width:54px;height:54px;border-radius:50%;background:var(--white)}
  .brand-name{font-family:"Montserrat",sans-serif;font-weight:800;font-size:36px;line-height:1.05;letter-spacing:-.5px}
  .front-rule{width:420px;height:3px;background:var(--white);margin:22px 0 16px}
  .tagline{font-family:"Montserrat",sans-serif;font-weight:500;font-size:20px;letter-spacing:8px}

  /* Back */
  .card-back{background:var(--white)}
  .services{position:absolute;left:40px;top:34px;display:flex;gap:14px}
  .services-title{writing-mode:vertical-rl;transform:rotate(180deg);font-family:"Montserrat",sans-serif;font-weight:700;font-size:17px;letter-spacing:3px;color:var(--orange)}
  .service-list{list-style:none;display:flex;flex-direction:column;gap:7px}
  .service-label{display:inline-block;background:var(--orange);color:var(--white);font-family:"Saira Condensed",sans-serif;font-weight:700;font-size:19px;letter-spacing:.5px;padding:1px 26px 0 8px;clip-path:polygon(0 0,100% 0,calc(100% - 14px) 100%,0 100%)}
  .service-detail{font-family:"Saira Condensed",sans-serif;font-weight:500;font-size:16px;color:var(--ink);padding-left:2px}
  .badge{position:absolute;right:40px;top:46px;width:150px;height:150px;border-radius:50%;background:var(--grey);display:flex;align-items:center;justify-content:center;text-align:center}
  .badge-name{font-family:"Montserrat",sans-serif;font-weight:700;font-size:15px;line-height:1.2;color:var(--white)}
  .motto-band{position:absolute;left:0;right:0;top:218px;height:34px;background:var(--ink);display:flex;align-items:center;justify-content:center}
  .motto{font-family:"Montserrat",sans-serif;font-weight:700;font-size:16px;letter-spacing:5px;color:var(--orange)}
  .contact{position:absolute;left:0;right:0;top:266px;text-align:center}
  .contact-label{font-family:"Montserrat",sans-serif;font-weight:700;font-size:15px;letter-spacing:3px;color:var(--orange)}
  .contact-phone{font-family:"Montserrat",sans-serif;font-weight:800;font-size:32px;letter-spacing:2px;color:var(--ink);margin-top:2px}
</style>
</head>
<body>
<main class="stage">
  <section class="card card-front" aria-label="Card front">
    <div class="brand">
      <span class="brand-dot"></span>
      <span class="brand-name">Halloran Field<br>Services</span>
    </div>
    <div class="front-rule"></div>
    <p class="tagline">CUSTOMISED SPREADING</p>
  </section>

  <section class="card card-back" aria-label="Card back">
    <div class="services">
      <h2 class="services-title">SERVICES</h2>
      <ul class="service-list">
        <li><span class="service-label">BULK FERTILIZER</span><p class="service-detail">including Lime, Gypsum, Manure &amp; Compost</p></li>
        <li><span class="service-label">GRANULAR FERTILIZER</span><p class="service-detail">including Single Super, Urea, Gran-am, &amp; Custom Blends</p></li>
        <li><span class="service-label">MODERN EQUIPMENT</span><p class="service-detail">Autosteer &amp; Variable Rate Capable</p></li>
      </ul>
    </div>
    <div class="badge"><span class="badge-name">Halloran<br>Field<br>Services</span></div>
    <div class="motto-band"><p class="motto">FRIENDLY &amp; RELIABLE SERVICE</p></div>
    <div class="contact">
      <p class="contact-label">CONTACT GUS</p>
      <p class="contact-phone">0417 552 308</p>
    </div>
  </section>
</main>
</body>
</html>
```